DESKHAVEN COSPACE Website design and coding

DESKHAVEN COSPACE

DESKHAVEN is Galveston’s first (and currently only) shared business co-working space. We share the same upscale, casual work environment, but we work independently on our own (or our team’s) projects and goals. For only a flat $195 membership fee per month, you have your very own all-inclusive, fun, personal business office environment. Website is written (Word file #12, below); and all pictures etc provided. Galveston is a beachy, coastal, historic city an hour from Houston, Texas USA. Logo (file 11 below) is temporary only.

Target Market(s)

Outside sales people, medical students looking for study hall, Houston companies looking for local office, real estate agents, graphic artists, entrepreneurs, etc

Contact Information for Business Card

will discuss --want to combine with current business card with multiple businesses

Logo Text

DESKHAVEN COSPACE

Coding

Coded - Design and coding required

Number of Pages Required

5+ page

Colors
ec1f27
fbed22

Requirements
Nice to have
• maroon/wine dominant with yellow and red accents, gray base are the colors of the space--website could coordinate--but open to creative ideas/combinations

```html
<!DOCTYPE html>
<html lang="en">
<head>
<meta charset="utf-8">
<title>Deskhaven Cospace – Contact</title>
<link href="https://fonts.googleapis.com/css2?family=Catamaran:wght@400;500;600;700;800&display=swap" rel="stylesheet">
<style>
:root{
  --maroon:#800000;
  --yellow:#fbd700;
  --base:#f2f2f2;
  --ink:#1f1f1f;
  --line:#d6d6d6;
  --white:#ffffff;
  --map:#e9e9e9;
}
*{box-sizing:border-box;margin:0;padding:0}
html,body{width:1200px;height:1200px;overflow:hidden;background:#ffffff}
body{position:relative;font-family:'Catamaran',sans-serif;color:var(--ink)}
.page{position:absolute;left:229px;top:0;width:1193px;height:1932px;transform:scale(.6211);transform-origin:0 0;background:var(--base);overflow:hidden}
.abs{position:absolute}
.topbar{left:0;top:0;width:1193px;height:60px;background:var(--maroon)}
.brand{left:111px;top:17px;font-size:20px;color:var(--yellow);letter-spacing:.5px}
.brand b{font-weight:700}
.nav a{position:absolute;top:20px;font-size:15px;color:var(--white);text-decoration:none}
.nav a.current{color:var(--yellow)}
.nav a.current::after{content:"";position:absolute;left:0;right:0;top:23px;height:3px;background:var(--yellow)}
.hero{left:0;top:60px;width:1193px;height:323px;background:linear-gradient(100deg,#8d8d8d 0%,#6a6a6a 35%,#5a534d 60%,#7c7c7c 100%)}
.hero-title{left:0;width:1193px;top:155px;text-align:center;font-size:48px;font-weight:700;color:var(--white)}
.crumb{left:0;width:1193px;top:240px;text-align:center;font-size:15px;color:var(--white)}
.crumb span{color:var(--yellow)}
h2.section{position:absolute;font-size:30px;font-weight:400;color:var(--maroon)}
h2.section b{font-weight:800}
.rule{position:absolute;width:87px;height:3px;background:var(--yellow)}
.details{left:112px;top:596px;font-size:14px;line-height:29.7px}
.details b{font-weight:700;margin-right:8px}
.details .in{padding-left:24px}
.form-card{left:527px;top:595px;width:554px;height:587px;background:var(--white);border-radius:6px;box-shadow:0 2px 12px rgba(0,0,0,.12)}
.label{position:absolute;font-size:13px;font-weight:500}
.field{position:absolute;width:223px;height:35px;border:1px solid var(--line);border-radius:6px;background:var(--white)}
.submit{left:570px;top:1103px;width:109px;height:42px;border-radius:21px;background:var(--maroon);color:var(--white);font-size:15px;font-weight:700;text-align:center;line-height:43px;box-shadow:0 3px 6px rgba(0,0,0,.2)}
.map{left:0;top:1220px;width:1193px;height:342px;background:var(--map)}
.footer{left:0;top:1562px;width:1193px;height:370px;background:var(--maroon);color:var(--white)}
.f-brand{left:112px;top:50px;color:var(--yellow);line-height:22px}
.f-brand .a{font-size:25px;font-weight:800}
.f-brand .b{font-size:20px;font-weight:400}
.f-tag{left:112px;top:126px;font-size:14px;line-height:24px}
.f-copy{left:118px;top:230px;font-size:8px}
.f-terms{left:133px;top:247px;font-size:8px;color:var(--yellow)}
.f-head{position:absolute;top:60px;font-size:18px;font-weight:700;color:var(--yellow)}
.f-list{position:absolute;top:126px;font-size:14px;line-height:23.6px}
.f-list .hl{color:var(--yellow)}
</style>
</head>
<body>
<div class="page">
  <header class="abs topbar">
    <div class="abs brand"><b>DESKHAVEN</b> COSPACE</div>
    <nav class="nav">
      <a style="left:679px">Home</a>
      <a style="left:751px">About</a>
      <a style="left:823px">Amenities</a>
      <a style="left:923px">Membership</a>
      <a class="current" style="left:1033px">Contact</a>
    </nav>
  </header>

  <section class="abs hero" role="img" aria-label="Photo of two professionals at work, one on a phone call"></section>
  <div class="abs hero-title">Contact</div>
  <div class="abs crumb"><span>Home</span> &nbsp;→&nbsp; Contact</div>

  <h2 class="section" style="left:112px;top:480px"><b>Contact</b> Details</h2>
  <div class="rule" style="left:112px;top:541px"></div>
  <h2 class="section" style="left:558px;top:485px"><b>Contact</b> Form</h2>
  <div class="rule" style="left:558px;top:546px"></div>

  <div class="abs details">
    <div><b>Email:</b> hello@deskhavencospace.com</div>
    <div><b>Phone:</b> 713-555-0148</div>
    <div><b>Facepage:</b> https://www.facepage.com/DeskhavenCospace</div>
    <div><b>WorkLink:</b> https://www.worklink.com/in/deskhaven</div>
    <div><b>Snapgram:</b> https://www.snapgram.com/deskhaven</div>
    <div><b>Office location:</b></div>
    <div class="in">Deskhaven Cospace</div>
    <div class="in">418 Harbor Ave, Suite 101</div>
    <div class="in">Galveston, TX 77550</div>
    <div><b>Owner:</b></div>
    <div class="in">Calder Holdings</div>
    <div class="in">mgmt@calderholdings.com</div>
    <div class="in">713-555-0148</div>
    <div><b>Mailing address for management:</b></div>
    <div class="in">Calder Holdings</div>
    <div class="in">275 Bayou St., Suite 200</div>
    <div class="in">Houston, TX 77002</div>
  </div>

  <div class="abs form-card"></div>
  <div class="label" style="left:570px;top:640px">First Name</div>
  <div class="label" style="left:823px;top:640px">Last Name</div>
  <div class="field" style="left:570px;top:661px"></div>
  <div class="field" style="left:811px;top:661px"></div>
  <div class="label" style="left:570px;top:710px">Address</div>
  <div class="label" style="left:823px;top:710px">City</div>
  <div class="field" style="left:570px;top:731px"></div>
  <div class="field" style="left:811px;top:731px"></div>
  <div class="label" style="left:570px;top:779px">State</div>
  <div class="label" style="left:823px;top:779px">Zip Code</div>
  <div class="field" style="left:570px;top:801px"></div>
  <div class="field" style="left:811px;top:801px"></div>
  <div class="label" style="left:570px;top:849px">Email</div>
  <div class="label" style="left:828px;top:849px">Phone</div>
  <div class="field" style="left:570px;top:871px"></div>
  <div class="field" style="left:811px;top:871px"></div>
  <div class="label" style="left:570px;top:918px">Description Of Business</div>
  <div class="field" style="left:570px;top:944px;width:469px"></div>
  <div class="label" style="left:570px;top:987px">Your Message</div>
  <div class="field" style="left:570px;top:1012px;width:469px;height:65px"></div>
  <div class="abs submit">Submit</div>

  <div class="abs map" role="img" aria-label="Street map of downtown Galveston marking the Deskhaven Cospace location"></div>

  <footer class="abs footer">
    <div class="abs f-brand"><div class="a">DESKHAVEN</div><div class="b">COSPACE</div></div>
    <div class="abs f-tag">Galveston's first &nbsp;shared business<br>co-working space</div>
    <div class="abs f-copy">©2020 Deskhaven. All Rights Reserved.</div>
    <div class="abs f-terms">Terms of Use <span style="color:#fff">|</span> Privacy Policy</div>

    <div class="f-head" style="left:475px">Menu</div>
    <div class="rule" style="left:475px;top:96px"></div>
    <div class="f-list" style="left:470px"><div class="hl">Home</div><div>About</div><div>Amenities</div><div>Membership</div><div>Contact</div></div>

    <div class="f-head" style="left:703px">Social</div>
    <div class="rule" style="left:703px;top:96px"></div>
    <div class="f-list" style="left:699px"><div>Facepage</div><div>WorkLink</div><div>Snapgram</div></div>

    <div class="f-head" style="left:930px">Contact</div>
    <div class="rule" style="left:930px;top:96px"></div>
    <div class="f-list" style="left:926px"><div>418 Harbor Ave.</div><div>Ste. 101</div><div>Galveston, TX 77550</div><div>713-555-0148</div><div class="hl">mgmt@calderholdings.com</div></div>
  </footer>
</div>
</body>
</html>
```